Heritage Hollow Business Cards

Require a business card design. <br/><br/>Needs to include logo (either round or long version) plus these details:<br/>Maya Torvell<br/>Heritage Hollow<br/>maya@kelvadtrading.com.au<br/>02 6481 7395<br/>PO Box Glenwarra NSW 2791<br/>www.heritagehollow.com.au<br/><br/>I need in an editable format so that I can create for multiple staff members. <br/><br/>

Target Market(s)

We are an online store selling renovation products to home owners are builders. Looking for a classic classy design.

Industry/Entity Type

Home And Garden

Contact Information for Business Card

Maya Torvell
Heritage Hollow
maya@kelvadtrading.com.au
02 6481 7395
PO Box Glenwarra NSW 2791
www.heritagehollow.com.au

Colors

Designer to choose colors to be used in the design.

Requirements
Must have
• Must include Logo.

```html
<!DOCTYPE html>
<html lang="en">
<head>
<meta charset="utf-8">
<title>Heritage Hollow Business Cards</title>
<link href="https://fonts.googleapis.com/css2?family=Work+Sans:wght@400;500;600&display=swap" rel="stylesheet">
<style>
  :root {
    --backdrop: #dcdcdc;
    --card-light: #ffffff;
    --card-dark: #1c1c1c;
    --ink: #1a1a1a;
    --ink-soft: #6e6e6e;
    --ink-muted: #888888;
    --paper: #f4f4f4;
    --ring-light: #8a8a8a;
    --ring-dark: #b9b9b9;
  }
  * { margin: 0; padding: 0; box-sizing: border-box; }
  html, body { width: 1200px; height: 1001px; overflow: hidden; }
  body {
    background: var(--backdrop);
    font-family: "Work Sans", Arial, sans-serif;
    position: relative;
  }
  .card {
    position: absolute;
    left: 306px;
    width: 587px;
    height: 335px;
  }
  .card--front { top: 135px; background: var(--card-light); }
  .card--back { top: 524px; background: var(--card-dark); }

  .brand-mark {
    position: absolute;
    border-radius: 50%;
    display: flex;
    align-items: center;
    justify-content: center;
    text-align: center;
    font-weight: 500;
    line-height: 1.1;
  }
  .card--front .brand-mark {
    left: 63px; top: 88px; width: 156px; height: 156px;
    border: 1px solid var(--ring-light);
    color: var(--ink);
    font-size: 21px;
  }
  .card--back .brand-mark {
    left: 189px; top: 0; margin-top: -1px;
    top: -1px;
    width: 226px; height: 226px;
    top: -1px;
    border: 1px solid var(--ring-dark);
    color: var(--paper);
    font-size: 30px;
  }
  .card--back .brand-mark { top: -1px; transform: translateY(0); top: -1px; }
  .card--back .brand-mark { top: -1px; }
  .card--back .brand-mark { top: -1px; }

  .divider {
    position: absolute;
    left: 256px; top: 82px;
    width: 2px; height: 181px;
    background: var(--ink);
  }
  .details { position: absolute; left: 290px; top: 79px; }
  .details__name { font-size: 25px; font-weight: 600; color: var(--ink); letter-spacing: 0.5px; line-height: 30px; }
  .details__role { font-size: 14px; color: var(--ink-muted); line-height: 18px; }
  .details__company { font-size: 14.5px; color: var(--ink); line-height: 18px; margin-top: 7px; }
  .details__address { font-size: 14.5px; color: var(--ink-soft); line-height: 20px; margin-top: 6px; }
  .contact { list-style: none; margin-top: 7px; }
  .contact li { display: flex; align-items: center; font-size: 14.5px; color: var(--ink-soft); line-height: 20px; }
  .contact svg { width: 11px; height: 11px; margin-right: 9px; flex-shrink: 0; }

  .back-url {
    position: absolute;
    left: 0; right: 0; top: 285px;
    text-align: center;
    color: var(--paper);
    font-size: 15px;
    letter-spacing: 2.6px;
  }
</style>
</head>
<body>
  <section class="card card--front">
    <div class="brand-mark" style="left:63px;top:88px;">Heritage<br>Hollow</div>
    <div class="divider"></div>
    <div class="details">
      <div class="details__name">Maya Torvell</div>
      <div class="details__role">Director</div>
      <div class="details__company">Heritage Hollow</div>
      <div class="details__address">PO Box Glenwarra<br>NSW 2791</div>
      <ul class="contact">
        <li>
          <svg viewBox="0 0 24 24" fill="#333"><path d="M6.6 10.8c1.4 2.8 3.8 5.1 6.6 6.6l2.2-2.2c.3-.3.7-.4 1-.2 1.1.4 2.3.6 3.6.6.6 0 1 .4 1 1V20c0 .6-.4 1-1 1C10.6 21 3 13.4 3 4c0-.6.4-1 1-1h3.5c.6 0 1 .4 1 1 0 1.3.2 2.5.6 3.6.1.3 0 .7-.2 1l-2.3 2.2z"/></svg>
          02 6481 7395
        </li>
        <li>
          <svg viewBox="0 0 24 24" fill="none" stroke="#333" stroke-width="2.4"><rect x="2" y="5" width="20" height="14"/><path d="M2 5l10 8 10-8"/></svg>
          maya@kelvadtrading.com.au
        </li>
        <li>
          <svg viewBox="0 0 24 24" fill="none" stroke="#333" stroke-width="2.2"><circle cx="12" cy="12" r="10"/><path d="M2 12h20M12 2c3 3 3 17 0 20M12 2c-3 3-3 17 0 20"/></svg>
          www.heritagehollow.com.au
        </li>
      </ul>
    </div>
  </section>

  <section class="card card--back">
    <div class="brand-mark" style="left:189px;top:0;transform:translateY(-1px);margin-top:0;top:0;">Heritage<br>Hollow</div>
    <div class="back-url">www.heritagehollow.com.au</div>
  </section>
</body>
</html>
```